Band and Coaching business card (creative industry)

My company The Fenwick Ensemble is the name of my band Soul outfit but is also a brand I use for my coaching business which is Performance coaching in the following areas: Corporate coaching, acting, vocals and dialect. The band plays for corporate events and private functions as well as local bar/restaurant/festivals.
Updates

Hi All

Please see updated info for the wording of the business card front and back.  This is ito then be followed with contact number, email and facebook link

first side should have:

JulieRose Brannigan
Creative Director
( followed by contact info as per previous)

Side 2:

The Fenwick Ensemble  - Band  
 Vocalist      I   Musician    I  Songwriter

The Fenwick Ensemble  - Studio
Performance Coaching  
Acting  I  Vocals  I Dialect  I Corporate Coaching

Industry/Entity Type

Events

Contact Information for Business Card

The Fenwick Ensemble (logo)
JulieRose Brannigan
Musician/Vocalist/Performance Coach
M: 0412 605 918
E: thefenwickensemble@mailbrook.net
W: www.friendspace.net/thefenwickensembleband

Font styles to use
Sans Serif

Requirements
Must have
• first side should have:

JulieRose Brannigan
Creative Director

Side 2:

The Fenwick Ensemble - Band
Vocalist I Musician I Songwriter

The Fenwick Ensemble - Studio
Performance Coaching
Acting I Vocals I Dialect I Corporate Coaching
Nice to have
• I like smaller business cards with curved edges.

some ideas for look in additional business cards attached.
Should not have
• music notes or anything specific to the field. Want to keep it funky and contemporary

```html
<!DOCTYPE html>
<html lang="en">
<head>
<meta charset="utf-8">
<title>The Fenwick Ensemble – Business Cards</title>
<link rel="stylesheet" href="https://fonts.googleapis.com/css2?family=Oswald:wght@400;500&family=Open+Sans:wght@400;600;700&display=swap">
<style>
  :root {
    --bg: #e4e4e6;
    --card: #ffffff;
    --magenta: #d12f8c;
    --magenta-deep: #b0318f;
    --violet: #8b3aa2;
    --ink-soft: #9a4aa6;
    --shadow: rgba(0, 0, 0, 0.14);
  }
  * { box-sizing: border-box; margin: 0; padding: 0; }
  html, body { width: 1200px; height: 750px; overflow: hidden; }
  body {
    background: var(--bg);
    font-family: "Open Sans", Arial, sans-serif;
    position: relative;
  }
  .card {
    position: absolute;
    width: 510px;
    height: 285px;
    background: var(--card);
    border-radius: 30px;
    box-shadow: 0 6px 18px var(--shadow);
    overflow: hidden;
  }
  .card--back { left: 60px; top: 110px; }
  .card--front { left: 630px; top: 355px; }

  /* shared brand mark */
  .brand { position: absolute; display: flex; flex-direction: column; align-items: center; gap: 8px; }
  .brand__dot {
    width: 112px; height: 112px; border-radius: 50%;
    background: linear-gradient(135deg, var(--magenta), var(--violet));
  }
  .brand__name {
    font-family: "Open Sans", Arial, sans-serif;
    font-weight: 700; font-size: 13px; white-space: nowrap;
  }

  /* back side */
  .card--back .brand { left: 197px; top: 48px; }
  .card--back .brand__name { color: var(--magenta); }
  .service { position: absolute; color: var(--magenta); }
  .service__title { font-weight: 700; font-size: 11.5px; }
  .service__line { font-size: 9px; color: var(--ink-soft); margin-top: 2px; }
  .service__line--strong { font-weight: 600; color: var(--magenta-deep); }
  .service--band { left: 26px; top: 192px; }
  .service--studio { left: 330px; top: 60px; width: 170px; }

  /* front side */
  .front__panel { position: absolute; inset: 0; }
  .card--front .brand { left: 360px; top: 50px; }
  .card--front .brand__dot { background: linear-gradient(135deg, #e04c9f, var(--violet)); border: 2px solid rgba(255,255,255,0.35); }
  .card--front .brand__name { color: #ffffff; }
  .person { position: absolute; left: 30px; top: 118px; }
  .person__name {
    font-family: "Oswald", "Arial Narrow", sans-serif;
    font-weight: 400; font-size: 30px; color: var(--magenta); line-height: 1;
  }
  .person__role { text-align: right; font-size: 10.5px; color: var(--ink-soft); margin-top: 2px; }
  .contact {
    position: absolute; left: 70px; top: 198px;
    border-left: 2px solid var(--magenta);
    padding-left: 14px; list-style: none;
  }
  .contact__item {
    display: flex; align-items: center; gap: 8px;
    font-size: 11px; color: var(--ink-soft); line-height: 20px;
  }
  .contact__icon { width: 11px; height: 11px; fill: var(--ink-soft); flex: none; }
</style>
</head>
<body>

  <section class="card card--back" aria-label="Business card, services side">
    <div class="service service--band">
      <p class="service__title">The Fenwick Ensemble - Band</p>
      <p class="service__line">Vocalist &nbsp;I&nbsp; Musician &nbsp;I&nbsp; Songwriter</p>
    </div>
    <div class="brand">
      <span class="brand__dot"></span>
      <span class="brand__name">The Fenwick Ensemble</span>
    </div>
    <div class="service service--studio">
      <p class="service__title">The Fenwick Ensemble - Studio</p>
      <p class="service__line service__line--strong">Performance Coaching</p>
      <p class="service__line">Acting I Vocals I Dialect I Corporate Coaching</p>
    </div>
  </section>

  <section class="card card--front" aria-label="Business card, contact side">
    <svg class="front__panel" viewBox="0 0 510 285" preserveAspectRatio="none" aria-hidden="true">
      <defs>
        <linearGradient id="panelFill" x1="0" y1="0" x2="1" y2="1">
          <stop offset="0" stop-color="#c3338e"/>
          <stop offset="1" stop-color="#a0359a"/>
        </linearGradient>
      </defs>
      <polygon points="215,0 510,0 510,285 380,285 340,62" fill="url(#panelFill)"/>
      <polygon points="215,0 300,0 335,58" fill="#ffffff"/>
    </svg>

    <div class="brand">
      <span class="brand__dot"></span>
      <span class="brand__name">The Fenwick Ensemble</span>
    </div>

    <div class="person">
      <h1 class="person__name">JulieRose Brannigan</h1>
      <p class="person__role">Creative Director</p>
    </div>

    <ul class="contact">
      <li class="contact__item">
        <svg class="contact__icon" viewBox="0 0 24 24"><path d="M6.6 10.8a15.1 15.1 0 0 0 6.6 6.6l2.2-2.2a1 1 0 0 1 1-.25 11.4 11.4 0 0 0 3.6.57 1 1 0 0 1 1 1V20a1 1 0 0 1-1 1A17 17 0 0 1 3 4a1 1 0 0 1 1-1h3.5a1 1 0 0 1 1 1c0 1.25.2 2.45.57 3.57a1 1 0 0 1-.25 1z"/></svg>
        <span>0412 605 918</span>
      </li>
      <li class="contact__item">
        <svg class="contact__icon" viewBox="0 0 24 24"><path d="M2 5h20v14H2z M4 7v.5l8 5 8-5V7z" fill-rule="evenodd"/></svg>
        <span>julierose@thefenwickensemble.net</span>
      </li>
      <li class="contact__item">
        <svg class="contact__icon" viewBox="0 0 24 24"><path d="M12 2a10 10 0 1 0 0 20 10 10 0 0 0 0-20zm0 2c.9 0 2.2 1.8 2.8 5H9.2C9.8 5.8 11.1 4 12 4zM4.3 11h4.7a17 17 0 0 0 0 2H4.3a8 8 0 0 1 0-2zm10.7 0h4.7a8 8 0 0 1 0 2H15a17 17 0 0 0 0-2zm-5.8 4h5.6c-.6 3.2-1.9 5-2.8 5s-2.2-1.8-2.8-5z"/></svg>
        <span>www.friendspace.net/thefenwickensembleband</span>
      </li>
    </ul>
  </section>

</body>
</html>
```